Step and Repeat Backdrop for wedding reception photo booth

Would like to have a Step and Repeat Backdrop (8 foot high by 10 foot wide) that incorporates the wedding logo (attached) and the names Helen and Gavin. Background should be white, and wedding colors are burgundy and gold. Show me creativity :-) I have included some random samples.

```html
<!DOCTYPE html>
<html lang="en">
<head>
<meta charset="utf-8">
<title>Helen &amp; Gavin — Step and Repeat Backdrop Options</title>
<link rel="stylesheet" href="https://fonts.googleapis.com/css2?family=Playfair+Display:wght@500&family=Cormorant+Garamond:wght@500&display=swap">
<style>
  :root {
    --page: #f4f4f4;
    --backdrop: #ffffff;
    --burgundy: #7f1230;
    --gold: #8f7418;
    --label: #3c3f47;
  }
  * { margin: 0; padding: 0; box-sizing: border-box; }
  html, body { width: 1200px; height: 1200px; overflow: hidden; background: var(--page); }
  .sheet {
    width: 1200px;
    height: 1200px;
    display: grid;
    grid-template-columns: 441px 441px;
    grid-template-rows: 420px 420px;
    column-gap: 125px;
    row-gap: 140px;
    padding: 95px 0 0 92px;
  }
  .option { display: flex; flex-direction: column; align-items: center; }
  .option-label {
    font-family: "Cormorant Garamond", serif;
    font-weight: 500;
    font-size: 27px;
    letter-spacing: 1px;
    color: var(--label);
    margin-bottom: 16px;
  }
  .backdrop {
    display: block;
    width: 441px;
    height: 361px;
    background: var(--backdrop);
    box-shadow: 0 2px 10px rgba(0,0,0,0.12);
  }
  .mono { font-family: "Playfair Display", serif; font-weight: 500; text-anchor: middle; dominant-baseline: central; }
  .repeat-65 .mono { font-size: 13px; }
  .repeat-103 .mono { font-size: 10px; }
  .centre-65 { font-size: 58px; }
  .centre-103 { font-size: 50px; }
  .gold { fill: var(--gold); }
  .burgundy { fill: var(--burgundy); }
</style>
</head>
<body>
<main class="sheet">

  <section class="option">
    <h2 class="option-label">65 LOGOS</h2>
    <svg class="backdrop" viewBox="0 0 441 361" aria-label="Backdrop with 65 repeated H&amp;G monograms and a large burgundy centre monogram">
      <g id="grid-65" class="repeat-65">
        <text class="mono gold" x="33" y="26">H&amp;G</text><text class="mono burgundy" x="88" y="26">H&amp;G</text><text class="mono gold" x="141" y="26">H&amp;G</text><text class="mono burgundy" x="195" y="26">H&amp;G</text><text class="mono gold" x="248" y="26">H&amp;G</text><text class="mono burgundy" x="300" y="26">H&amp;G</text><text class="mono gold" x="353" y="26">H&amp;G</text><text class="mono burgundy" x="405" y="26">H&amp;G</text>
        <text class="mono burgundy" x="33" y="64">H&amp;G</text><text class="mono gold" x="88" y="64">H&amp;G</text><text class="mono burgundy" x="141" y="64">H&amp;G</text><text class="mono gold" x="195" y="64">H&amp;G</text><text class="mono burgundy" x="248" y="64">H&amp;G</text><text class="mono gold" x="300" y="64">H&amp;G</text><text class="mono burgundy" x="353" y="64">H&amp;G</text><text class="mono gold" x="405" y="64">H&amp;G</text>
        <text class="mono gold" x="33" y="104">H&amp;G</text><text class="mono burgundy" x="88" y="104">H&amp;G</text><text class="mono gold" x="141" y="104">H&amp;G</text><text class="mono burgundy" x="195" y="104">H&amp;G</text><text class="mono gold" x="248" y="104">H&amp;G</text><text class="mono burgundy" x="300" y="104">H&amp;G</text><text class="mono gold" x="353" y="104">H&amp;G</text><text class="mono burgundy" x="405" y="104">H&amp;G</text>
        <text class="mono burgundy" x="33" y="143">H&amp;G</text><text class="mono gold" x="88" y="143">H&amp;G</text><text class="mono burgundy" x="128" y="143">H&amp;G</text><text class="mono gold" x="316" y="143">H&amp;G</text><text class="mono burgundy" x="353" y="143">H&amp;G</text><text class="mono gold" x="405" y="143">H&amp;G</text>
        <text class="mono gold" x="33" y="181">H&amp;G</text><text class="mono burgundy" x="88" y="181">H&amp;G</text><text class="mono gold" x="128" y="181">H&amp;G</text><text class="mono burgundy" x="316" y="181">H&amp;G</text><text class="mono gold" x="353" y="181">H&amp;G</text><text class="mono burgundy" x="405" y="181">H&amp;G</text>
        <text class="mono burgundy" x="33" y="221">H&amp;G</text><text class="mono gold" x="88" y="221">H&amp;G</text><text class="mono burgundy" x="128" y="221">H&amp;G</text><text class="mono gold" x="316" y="221">H&amp;G</text><text class="mono burgundy" x="353" y="221">H&amp;G</text><text class="mono gold" x="405" y="221">H&amp;G</text>
        <text class="mono gold" x="33" y="260">H&amp;G</text><text class="mono burgundy" x="88" y="260">H&amp;G</text><text class="mono gold" x="128" y="260">H&amp;G</text><text class="mono burgundy" x="316" y="260">H&amp;G</text><text class="mono gold" x="353" y="260">H&amp;G</text><text class="mono burgundy" x="405" y="260">H&amp;G</text>
        <text class="mono burgundy" x="33" y="299">H&amp;G</text><text class="mono gold" x="88" y="299">H&amp;G</text><text class="mono burgundy" x="141" y="299">H&amp;G</text><text class="mono gold" x="195" y="299">H&amp;G</text><text class="mono burgundy" x="248" y="299">H&amp;G</text><text class="mono gold" x="300" y="299">H&amp;G</text><text class="mono burgundy" x="353" y="299">H&amp;G</text><text class="mono gold" x="405" y="299">H&amp;G</text>
        <text class="mono gold" x="33" y="338">H&amp;G</text><text class="mono burgundy" x="88" y="338">H&amp;G</text><text class="mono gold" x="141" y="338">H&amp;G</text><text class="mono burgundy" x="195" y="338">H&amp;G</text><text class="mono gold" x="248" y="338">H&amp;G</text><text class="mono burgundy" x="300" y="338">H&amp;G</text><text class="mono gold" x="353" y="338">H&amp;G</text><text class="mono burgundy" x="405" y="338">H&amp;G</text>
      </g>
      <text class="mono centre-65 burgundy" x="221" y="203">H&amp;G</text>
    </svg>
  </section>

  <section class="option">
    <h2 class="option-label">65 LOGOS</h2>
    <svg class="backdrop" viewBox="0 0 441 361" aria-label="Backdrop with 65 repeated H&amp;G monograms and a large gold centre monogram">
      <use href="#grid-65"/>
      <text class="mono centre-65 gold" x="221" y="203">H&amp;G</text>
    </svg>
  </section>

  <section class="option">
    <h2 class="option-label">103 LOGOS</h2>
    <svg class="backdrop" viewBox="0 0 441 361" aria-label="Backdrop with 103 repeated H&amp;G monograms and a large burgundy centre monogram">
      <g id="grid-103" class="repeat-103">
        <text class="mono gold" x="30" y="27">H&amp;G</text><text class="mono burgundy" x="72" y="27">H&amp;G</text><text class="mono gold" x="114" y="27">H&amp;G</text><text class="mono burgundy" x="157" y="27">H&amp;G</text><text class="mono gold" x="200" y="27">H&amp;G</text><text class="mono burgundy" x="242" y="27">H&amp;G</text><text class="mono gold" x="284" y="27">H&amp;G</text><text class="mono burgundy" x="325" y="27">H&amp;G</text><text class="mono gold" x="366" y="27">H&amp;G</text><text class="mono burgundy" x="408" y="27">H&amp;G</text>
        <text class="mono burgundy" x="30" y="58">H&amp;G</text><text class="mono gold" x="72" y="58">H&amp;G</text><text class="mono burgundy" x="114" y="58">H&amp;G</text><text class="mono gold" x="157" y="58">H&amp;G</text><text class="mono burgundy" x="200" y="58">H&amp;G</text><text class="mono gold" x="242" y="58">H&amp;G</text><text class="mono burgundy" x="284" y="58">H&amp;G</text><text class="mono gold" x="325" y="58">H&amp;G</text><text class="mono burgundy" x="366" y="58">H&amp;G</text><text class="mono gold" x="408" y="58">H&amp;G</text>
        <text class="mono gold" x="30" y="88">H&amp;G</text><text class="mono burgundy" x="72" y="88">H&amp;G</text><text class="mono gold" x="114" y="88">H&amp;G</text><text class="mono burgundy" x="157" y="88">H&amp;G</text><text class="mono gold" x="200" y="88">H&amp;G</text><text class="mono burgundy" x="242" y="88">H&amp;G</text><text class="mono gold" x="284" y="88">H&amp;G</text><text class="mono burgundy" x="325" y="88">H&amp;G</text><text class="mono gold" x="366" y="88">H&amp;G</text><text class="mono burgundy" x="408" y="88">H&amp;G</text>
        <text class="mono burgundy" x="30" y="120">H&amp;G</text><text class="mono gold" x="72" y="120">H&amp;G</text><text class="mono burgundy" x="114" y="120">H&amp;G</text><text class="mono gold" x="157" y="120">H&amp;G</text><text class="mono burgundy" x="200" y="120">H&amp;G</text><text class="mono gold" x="242" y="120">H&amp;G</text><text class="mono burgundy" x="284" y="120">H&amp;G</text><text class="mono gold" x="325" y="120">H&amp;G</text><text class="mono burgundy" x="366" y="120">H&amp;G</text><text class="mono gold" x="408" y="120">H&amp;G</text>
        <text class="mono gold" x="30" y="151">H&amp;G</text><text class="mono burgundy" x="72" y="151">H&amp;G</text><text class="mono gold" x="114" y="151">H&amp;G</text><text class="mono burgundy" x="147" y="151">H&amp;G</text><text class="mono gold" x="296" y="151">H&amp;G</text><text class="mono burgundy" x="325" y="151">H&amp;G</text><text class="mono gold" x="366" y="151">H&amp;G</text><text class="mono burgundy" x="408" y="151">H&amp;G</text>
        <text class="mono burgundy" x="30" y="182">H&amp;G</text><text class="mono gold" x="72" y="182">H&amp;G</text><text class="mono burgundy" x="114" y="182">H&amp;G</text><text class="mono gold" x="147" y="182">H&amp;G</text><text class="mono burgundy" x="296" y="182">H&amp;G</text><text class="mono gold" x="325" y="182">H&amp;G</text><text class="mono burgundy" x="366" y="182">H&amp;G</text><text class="mono gold" x="408" y="182">H&amp;G</text>
        <text class="mono gold" x="30" y="212">H&amp;G</text><text class="mono burgundy" x="72" y="212">H&amp;G</text><text class="mono gold" x="114" y="212">H&amp;G</text><text class="mono burgundy" x="147" y="212">H&amp;G</text><text class="mono gold" x="296" y="212">H&amp;G</text><text class="mono burgundy" x="325" y="212">H&amp;G</text><text class="mono gold" x="366" y="212">H&amp;G</text><text class="mono burgundy" x="408" y="212">H&amp;G</text>
        <text class="mono burgundy" x="30" y="243">H&amp;G</text><text class="mono gold" x="72" y="243">H&amp;G</text><text class="mono burgundy" x="114" y="243">H&amp;G</text><text class="mono gold" x="147" y="243">H&amp;G</text><text class="mono burgundy" x="296" y="243">H&amp;G</text><text class="mono gold" x="325" y="243">H&amp;G</text><text class="mono burgundy" x="366" y="243">H&amp;G</text><text class="mono gold" x="408" y="243">H&amp;G</text>
        <text class="mono gold" x="30" y="274">H&amp;G</text><text class="mono burgundy" x="72" y="274">H&amp;G</text><text class="mono gold" x="114" y="274">H&amp;G</text><text class="mono burgundy" x="157" y="274">H&amp;G</text><text class="mono gold" x="200" y="274">H&amp;G</text><text class="mono burgundy" x="242" y="274">H&amp;G</text><text class="mono gold" x="284" y="274">H&amp;G</text><text class="mono burgundy" x="325" y="274">H&amp;G</text><text class="mono gold" x="366" y="274">H&amp;G</text><text class="mono burgundy" x="408" y="274">H&amp;G</text>
        <text class="mono burgundy" x="30" y="305">H&amp;G</text><text class="mono gold" x="72" y="305">H&amp;G</text><text class="mono burgundy" x="114" y="305">H&amp;G</text><text class="mono gold" x="157" y="305">H&amp;G</text><text class="mono burgundy" x="200" y="305">H&amp;G</text><text class="mono gold" x="242" y="305">H&amp;G</text><text class="mono burgundy" x="284" y="305">H&amp;G</text><text class="mono gold" x="325" y="305">H&amp;G</text><text class="mono burgundy" x="366" y="305">H&amp;G</text><text class="mono gold" x="408" y="305">H&amp;G</text>
        <text class="mono gold" x="30" y="335">H&amp;G</text><text class="mono burgundy" x="72" y="335">H&amp;G</text><text class="mono gold" x="114" y="335">H&amp;G</text><text class="mono burgundy" x="157" y="335">H&amp;G</text><text class="mono gold" x="200" y="335">H&amp;G</text><text class="mono burgundy" x="242" y="335">H&amp;G</text><text class="mono gold" x="284" y="335">H&amp;G</text><text class="mono burgundy" x="325" y="335">H&amp;G</text><text class="mono gold" x="366" y="335">H&amp;G</text><text class="mono burgundy" x="408" y="335">H&amp;G</text>
      </g>
      <text class="mono centre-103 burgundy" x="222" y="199">H&amp;G</text>
    </svg>
  </section>

  <section class="option">
    <h2 class="option-label">103 LOGOS</h2>
    <svg class="backdrop" viewBox="0 0 441 361" aria-label="Backdrop with 103 repeated H&amp;G monograms and a large gold centre monogram">
      <use href="#grid-103"/>
      <text class="mono centre-103 gold" x="222" y="199">H&amp;G</text>
    </svg>
  </section>

</main>
</body>
</html>
```